Business cards for a fun web development agency

Hi,I am building a web development agency. You can read about it on the website http://kite-loft.examplehost.com. Basically, I want to focus on free and open source products and stay as far away from the corporate business feeling as possible. I want to build a community so I want the business card to feel fun and approachable (at the risk of professional if need be). I am uploading some of my image assets in various file formats. Feel free to use them or make your own if you want just keeping in theme with the website.
Industry/Entity Type
Building
Contact Information for Business Card
Company Name: Boat ShedWebsite: www.kiteloftdev.example (it's currently in alpha on http://kite-loft.examplehost.com if you want to see the them we are trying to capture)My name is: Banner B. SchaferMy email: banner@boatsheddev.comMy phone: 0431 587 904
Look and feel

```html
<!DOCTYPE html>
<html lang="en">
<head>
<meta charset="utf-8">
<title>Kite Loft – Business Cards</title>
<link rel="stylesheet" href="https://fonts.googleapis.com/css2?family=Arimo:wght@400&display=swap">
<style>
  :root {
    --brand-blue: #1b8cc4;
    --card-white: #fbfbfb;
    --card-grey: #d9dadc;
    --backdrop: #ececee;
  }
  * { box-sizing: border-box; margin: 0; padding: 0; }
  html, body {
    width: 1200px; height: 862px; overflow: hidden;
    background: var(--backdrop);
    font-family: "Arimo", Arial, sans-serif;
  }
  .sheet {
    position: relative; width: 1200px; height: 862px;
    display: flex; justify-content: center; align-items: center; gap: 90px;
  }
  .card {
    position: relative; width: 340px; height: 595px; overflow: hidden;
    background: linear-gradient(170deg, var(--card-white) 0%, #f1f1f2 45%, var(--card-grey) 100%);
    box-shadow: 0 6px 24px rgba(0,0,0,0.12);
  }
  .card-texture {
    position: absolute; inset: 0;
    background: linear-gradient(125deg, rgba(255,255,255,0.5) 0%, rgba(255,255,255,0) 40%, rgba(0,0,0,0.04) 70%, rgba(255,255,255,0.2) 100%);
  }
  .wordmark {
    position: absolute; left: 0; right: 0; text-align: center;
    color: var(--brand-blue); font-weight: 400; font-size: 40px; letter-spacing: 1px;
  }
  .card-front .wordmark { top: 94px; }
  .card-back .wordmark { top: 152px; }
  .holder-name {
    position: absolute; left: 38px; top: 208px;
    color: var(--brand-blue); font-size: 27px; font-weight: 400;
  }
  .contact-list {
    position: absolute; left: 38px; top: 282px; list-style: none;
    color: var(--brand-blue); font-size: 17px; line-height: 30px;
  }
  .contact-list li { display: flex; align-items: center; gap: 10px; }
  .contact-list svg { width: 13px; height: 13px; fill: var(--brand-blue); flex: none; }
  .services { position: absolute; left: 38px; top: 430px; color: var(--brand-blue); }
  .services-title { font-size: 20px; font-weight: 400; margin-bottom: 14px; }
  .services-list { list-style: none; font-size: 17.5px; line-height: 28px; }
  .services-list li::before { content: "\2733"; font-size: 12px; margin-right: 10px; vertical-align: 2px; }
  .back-artwork {
    position: absolute; left: 0; right: 0; bottom: 0; height: 260px;
    background: linear-gradient(180deg, rgba(27,140,196,0) 0%, rgba(27,140,196,0.28) 45%, rgba(27,140,196,0.4) 100%);
  }
</style>
</head>
<body>
<main class="sheet">
  <section class="card card-front" aria-label="Card front">
    <div class="card-texture" role="img" aria-label="Soft grey low-poly paper texture"></div>
    <div class="wordmark">Kite Loft</div>
    <h1 class="holder-name">Corwin T. Aldous</h1>
    <ul class="contact-list">
      <li><svg viewBox="0 0 16 16"><path d="M3 1l3 0 1 4-2 1c1 2 3 4 5 5l1-2 4 1 0 3c0 1-1 2-2 2C7 15 1 9 1 3c0-1 1-2 2-2z"/></svg>0431 587 904</li>
      <li><svg viewBox="0 0 16 16"><circle cx="8" cy="8" r="7" fill="none" stroke="#1b8cc4" stroke-width="2"/><path d="M1 8h14M8 1c3 3 3 11 0 14M8 1c-3 3-3 11 0 14" fill="none" stroke="#1b8cc4" stroke-width="1.4"/></svg>www.kiteloftdev.example</li>
      <li><svg viewBox="0 0 16 16"><path d="M1 3h14v10H1z"/><path d="M1 3l7 6 7-6" fill="none" stroke="#fff" stroke-width="1.4"/></svg>corwin@kiteloftdev.example</li>
    </ul>
    <div class="services">
      <h2 class="services-title">Services :</h2>
      <ul class="services-list">
        <li>Open Source Software</li>
        <li>Consulting For Developers</li>
        <li>Web Development For Muggles</li>
      </ul>
    </div>
  </section>

  <section class="card card-back" aria-label="Card back">
    <div class="card-texture" role="img" aria-label="Soft grey low-poly paper texture"></div>
    <div class="wordmark">Kite Loft</div>
    <div class="back-artwork" role="img" aria-label="Large faded brand artwork in soft blue"></div>
  </section>
</main>
</body>
</html>
```